Holiday Rental Company Flyer Design (DL not A5)

Note from Brandloom Administration: The category sizing selected is A5, however the project requires DL sized artwork. Please refer to the DL template link below while the 'Special Requirements' are updated accordingly.

Project Brief:
We need a double sided DL flyer designed for an up market Holiday Rental Company that portrays a personalised approach to property management. These are to be used for letter box drops to homes we're specifically targeting so the design should be modern, complimentary colour palette, uncluttered & visually appealing.

Please Download the DL Template from Quillora here: http://www.quillora.com.au/ql/ns/propath/UploadResources.aspx?selectedTab=0?pfid=KMT&pf_id=KMT&xnav=easypath-upload-image#Templates

Target Market(s)

Wealthy Home Owners

Industry/Entity Type

It Company

Other font styles liked:
• Avant Garde Extra Light & Demi

Colors
33b8a4

Requirements
Must have
• DL Flyer sizes (210mm width x 99mm width, plus 3mm bleed)
• Front: Logo, Main Image & Grab
• Back: Contact Details & Brief Description of our business
• Images: Ideally the main image should be the house with the pool but alternatively a lifestyle images could also be used.
Nice to have
• A creative designer!
Should not have
• Clutter & busy designs

```html
<!DOCTYPE html>
<html lang="en">
<head>
<meta charset="utf-8">
<title>Harbourline Stays – DL Flyer Back</title>
<link rel="stylesheet" href="https://fonts.googleapis.com/css2?family=Poppins:wght@200;300;500&display=swap">
<style>
  :root {
    --page-bg: #e6e8e4;
    --charcoal: #3a3a3a;
    --ink: #222222;
    --soft-ink: #555555;
    --panel-light: #f1f8fb;
    --teal: #33b8a4;
    --teal-soft: #8fd3cb;
    --white: #ffffff;
    --photo-light: #d6d6d4;
    --photo-mid: #a9aaa8;
    --photo-dark: #7d7f7d;
  }
  * { box-sizing: border-box; margin: 0; padding: 0; }
  html, body {
    width: 1200px; height: 900px; overflow: hidden;
    background: var(--page-bg);
    font-family: "Poppins", sans-serif;
  }
  .flyer {
    position: absolute; left: 71px; top: 201px;
    width: 1058px; height: 498px;
    background: var(--panel-light);
    overflow: hidden;
    box-shadow: 0 4px 14px rgba(0,0,0,0.18);
  }
  .lifestyle-photo {
    position: absolute; left: 0; top: 0; width: 346px; height: 498px;
    background: linear-gradient(160deg, var(--photo-light) 0%, var(--photo-mid) 55%, var(--photo-dark) 100%);
  }
  .photo-accent-bar {
    position: absolute; left: 22px; top: 0; width: 5px; height: 96px;
    background: rgba(255,255,255,0.8);
  }
  .headline-band {
    position: absolute; left: 0; top: 252px; width: 311px; height: 81px;
    background: rgba(255,255,255,0.6);
  }
  .headline {
    position: absolute; left: 74px; top: 254px;
    font-weight: 200; font-size: 31px; line-height: 32px; color: var(--ink);
  }
  .headline-rule {
    position: absolute; left: 92px; top: 349px; width: 254px; height: 2px;
    background: var(--white);
  }
  .corner-shapes { position: absolute; left: 256px; top: 418px; }
  .intro-panel {
    position: absolute; left: 346px; top: 0; width: 351px; height: 248px;
    background: var(--charcoal);
  }
  .brand-name {
    position: absolute; left: 0; top: 34px; width: 100%;
    text-align: center; font-weight: 300; font-size: 15px;
    letter-spacing: 2px; color: #9a9a9a;
  }
  .intro-text {
    position: absolute; left: 61px; top: 96px; width: 240px;
    font-weight: 200; font-size: 16px; line-height: 20px; color: #b5b5b5;
  }
  .junction-badge { position: absolute; left: 324px; top: 226px; }
  .contact {
    position: absolute; left: 740px; top: 32px; width: 300px;
  }
  .contact-lead {
    text-align: center; font-weight: 200; font-size: 13.5px;
    line-height: 17.5px; color: var(--soft-ink);
  }
  .contact-icons { display: flex; gap: 8px; margin: 31px 0 0 37px; }
  .contact-details { margin: 16px 0 0 38px; font-weight: 500; color: var(--ink); }
  .contact-phone { font-size: 16px; line-height: 22px; }
  .contact-line { font-size: 14px; line-height: 22px; }
  .contact-web { color: var(--teal); }
  .contact-rule {
    width: 196px; height: 2px; background: var(--teal); margin: 21px 0 0 38px;
  }
  .service-text {
    position: absolute; left: 442px; top: 310px; width: 190px;
    font-weight: 300; font-size: 16px; line-height: 21.5px; color: var(--soft-ink);
  }
  .benefits { position: absolute; left: 670px; top: 312px; list-style: none; }
  .benefit {
    position: relative; padding-left: 29px; margin-bottom: 12px;
    font-weight: 500; font-size: 13.5px; line-height: 19px; color: var(--ink);
  }
  .benefit svg { position: absolute; left: 0; top: 10px; }
</style>
</head>
<body>
  <main class="flyer">
    <div class="lifestyle-photo" role="img" aria-label="Lifestyle photo: white flowers in a vase beside a bathroom basin against grey tiles"></div>
    <div class="photo-accent-bar"></div>
    <div class="headline-band"></div>
    <h1 class="headline">What we do<br>differently</h1>
    <div class="headline-rule"></div>
    <svg class="corner-shapes" width="80" height="80" viewBox="0 0 80 80" aria-hidden="true">
      <polygon points="0,40 40,40 40,0" fill="#ffffff" opacity="0.85"/>
      <polygon points="40,40 80,40 80,0" fill="#d9dcdb" opacity="0.9"/>
      <polygon points="0,80 40,40 40,80" fill="#c2c6c5" opacity="0.9"/>
      <polygon points="40,80 80,40 80,80" fill="#ffffff" opacity="0.9"/>
    </svg>

    <section class="intro-panel">
      <p class="brand-name">HARBOURLINE STAYS</p>
      <p class="intro-text">Rather than relying upon a key safe or a central pick-up destination, a ‘Harbourline Stays’ staff member will greet guests upon arrival.</p>
    </section>

    <svg class="junction-badge" width="44" height="44" viewBox="0 0 44 44" aria-hidden="true">
      <circle cx="22" cy="22" r="20" fill="#ffffff" stroke="#333" stroke-width="1.5"/>
      <path d="M22 22 L22 2 A20 20 0 0 0 2 22 Z" fill="var(--teal)"/>
      <path d="M22 22 L42 22 A20 20 0 0 1 22 42 Z" fill="var(--teal-soft)"/>
      <line x1="2" y1="22" x2="42" y2="22" stroke="#333" stroke-width="1.2"/>
      <line x1="22" y1="2" x2="22" y2="42" stroke="#333" stroke-width="1.2"/>
    </svg>

    <section class="contact">
      <p class="contact-lead">If you’d like to know what your property could achieve or require additional information, please contact us on:</p>
      <div class="contact-icons" aria-hidden="true">
        <svg width="36" height="36" viewBox="0 0 36 36"><circle cx="18" cy="18" r="16.5" fill="none" stroke="#222" stroke-width="2"/><path d="M12 10 l4 0 l1.5 4.5 l-2.5 2 a11 11 0 0 0 5 5 l2-2.5 l4.5 1.5 l0 4 a2 2 0 0 1 -2 1.5 a15 15 0 0 1 -14 -14 a2 2 0 0 1 1.5 -2z" fill="#222"/></svg>
        <svg width="36" height="36" viewBox="0 0 36 36"><circle cx="18" cy="18" r="16.5" fill="none" stroke="#222" stroke-width="2"/><rect x="10" y="12" width="16" height="12" fill="none" stroke="#222" stroke-width="2"/><path d="M10 12 L18 19 L26 12" fill="none" stroke="#222" stroke-width="2"/></svg>
        <svg width="36" height="36" viewBox="0 0 36 36"><circle cx="18" cy="18" r="16.5" fill="none" stroke="#222" stroke-width="2"/><rect x="10" y="11" width="16" height="11" fill="none" stroke="#222" stroke-width="2"/><path d="M18 22 v4 M13 26 h10" stroke="#222" stroke-width="2"/></svg>
        <svg width="36" height="36" viewBox="0 0 36 36"><circle cx="18" cy="18" r="16.5" fill="none" stroke="#222" stroke-width="2"/><path d="M18 28 C13 21 12 18 12 16 a6 6 0 0 1 12 0 c0 2 -1 5 -6 12z" fill="none" stroke="#222" stroke-width="2"/><circle cx="18" cy="16" r="2" fill="#222"/></svg>
      </div>
      <div class="contact-details">
        <p class="contact-phone">03 5900 1472</p>
        <p class="contact-line">stay@harbourlinestays.com.au</p>
        <p class="contact-line contact-web">harbourlinestays.com.au</p>
        <p class="contact-line">PO Box 18, Seacliff Victoria 3999</p>
      </div>
      <div class="contact-rule"></div>
    </section>

    <p class="service-text">Our ‘Meet &amp; Greet’ service provides home owners with an increased level of Security and also allows us to:</p>

    <ul class="benefits">
      <li class="benefit"><svg width="14" height="14" viewBox="0 0 14 14" aria-hidden="true"><polygon points="7,1 13,5.5 10.7,12.5 3.3,12.5 1,5.5" fill="none" stroke="var(--teal)" stroke-width="1.6"/></svg>Establish a rapport &amp; help<br>facilitate future bookings</li>
      <li class="benefit"><svg width="14" height="14" viewBox="0 0 14 14" aria-hidden="true"><polygon points="7,1 13,5.5 10.7,12.5 3.3,12.5 1,5.5" fill="none" stroke="var(--teal)" stroke-width="1.6"/></svg>Prepare the home for their arrival<br>(lights, heaters, music etc.)</li>
      <li class="benefit"><svg width="14" height="14" viewBox="0 0 14 14" aria-hidden="true"><polygon points="7,1 13,5.5 10.7,12.5 3.3,12.5 1,5.5" fill="none" stroke="var(--teal)" stroke-width="1.6"/></svg>Reiterate their responsibilities to<br>ensure the return of their bond</li>
    </ul>
  </main>
</body>
</html>
```